letterhead design using our existing logo

We are a small boutique property management business based in Sydney's Northern Beaches.
We are after a sleek, simple modern letterhead (A4) incorporating our logo and its colours.
Also matching envelope (DL)
I have attached the logo with black text and white text for design options.

Target Market(s)

29-69yo Male and Female

Industry/Entity Type

Property Management

Requirements
Must have
• - Harbourline Estates logo
• - Address, number and website:
• Suite 7, 12-14 Wattlegrove Parade, Manly NSW 2095
• Tel: Carl Dorsey 0491 570 163 Marisol Quade 0491 570 218 www.harbourlinestatesgroup.com.au
Nice to have
• sleek design that looks modern and professional
Should not have
• too many colours or too busy

```html
<!DOCTYPE html>
<html lang="en">
<head>
<meta charset="utf-8">
<title>Harbourline Estates – Letterhead &amp; DL Envelope</title>
<link rel="stylesheet" href="https://fonts.googleapis.com/css2?family=Arimo:wght@400;700&display=swap">
<style>
  :root {
    --teal: #137b8b;
    --teal-light: #3aa6b2;
    --ink: #1c1c1c;
    --paper: #ffffff;
    --backdrop: #e6e8e9;
    --shadow: rgba(0, 0, 0, 0.18);
  }
  * { box-sizing: border-box; margin: 0; padding: 0; }
  html, body {
    width: 1200px;
    height: 1000px;
    overflow: hidden;
  }
  body {
    position: relative;
    background: var(--backdrop);
    font-family: "Arimo", Arial, sans-serif;
  }
  .sheet {
    position: absolute;
    background: var(--paper);
    box-shadow: 0 4px 14px var(--shadow);
    overflow: hidden;
  }
  .letterhead { left: 32px; top: 78px; width: 595px; height: 842px; }
  .envelope-front { left: 531px; top: 190px; width: 623px; height: 310px; }
  .envelope-back { left: 541px; top: 520px; width: 622px; height: 310px; }

  .brand-name {
    position: absolute;
    font-family: "Arimo", Arial, sans-serif;
    font-weight: 700;
    font-size: 23px;
    letter-spacing: -0.2px;
    color: var(--ink);
    white-space: nowrap;
  }
  .letterhead .brand-name { left: 25px; top: 57px; }
  .envelope-front .brand-name { left: 22px; top: 59px; }

  .footer-band {
    position: absolute;
    left: 0;
    bottom: 0;
    width: 100%;
  }
  .footer-band svg { display: block; }

  .contact-block {
    position: absolute;
    color: #ffffff;
    font-size: 11px;
    line-height: 13.4px;
    font-style: normal;
    white-space: nowrap;
  }
  .letterhead .contact-block { left: 24px; bottom: 8px; }
  .envelope-front .contact-block { left: 25px; bottom: 7px; }

  .web-line {
    position: absolute;
    color: var(--teal);
    font-size: 9.5px;
    white-space: nowrap;
  }
  .letterhead .web-line { right: 12px; bottom: 22px; }
  .envelope-front .web-line { right: 20px; bottom: 21px; }

  .flap {
    position: absolute;
    left: 0;
    top: 0;
    width: 100%;
    height: 108px;
    background: var(--teal);
    border-bottom-left-radius: 46px;
    box-shadow: 0 3px 4px rgba(0, 0, 0, 0.08);
  }
  .flap-web {
    position: absolute;
    left: 0;
    right: 0;
    top: 49px;
    text-align: center;
    color: #ffffff;
    font-size: 10px;
    letter-spacing: 2.4px;
  }
</style>
</head>
<body>

  <section class="sheet letterhead">
    <div class="brand-name">HARBOURLINE ESTATES</div>

    <div class="footer-band">
      <svg width="595" height="73" viewBox="0 0 595 73">
        <polygon points="0,0 200,0 247,58 595,58 595,73 0,73" fill="var(--teal)"/>
        <polygon points="200,0 210,0 257,58 247,58" fill="var(--teal-light)"/>
        <rect x="247" y="58" width="348" height="3" fill="var(--teal-light)"/>
      </svg>
    </div>
    <address class="contact-block">
      Suite 7, 12-14 Wattlegrove Parade<br>
      Manly NSW 2095<br>
      Carl Dorsey 0491 570 163<br>
      Marisol Quade 0491 570 218
    </address>
    <div class="web-line">info@harbourlinestatesgroup.com.au&nbsp;I&nbsp;www.harbourlinestatesgroup.com.au</div>
  </section>

  <section class="sheet envelope-front">
    <div class="brand-name">HARBOURLINE ESTATES</div>

    <div class="footer-band">
      <svg width="623" height="72" viewBox="0 0 623 72">
        <polygon points="0,0 200,0 250,57 623,57 623,72 0,72" fill="var(--teal)"/>
        <polygon points="200,0 210,0 260,57 250,57" fill="var(--teal-light)"/>
        <rect x="250" y="57" width="373" height="3" fill="var(--teal-light)"/>
      </svg>
    </div>
    <address class="contact-block">
      Suite 7, 12-14 Wattlegrove Parade<br>
      Manly NSW 2095<br>
      Carl Dorsey 0491 570 163<br>
      Marisol Quade 0491 570 218
    </address>
    <div class="web-line">info@harbourlinestatesgroup.com.au&nbsp;I&nbsp;www.harbourlinestatesgroup.com.au</div>
  </section>

  <section class="sheet envelope-back">
    <div class="flap">
      <div class="flap-web">www.harbourlinestatesgroup.com.au</div>
    </div>
  </section>

</body>
</html>
```